PostCard Design Project

I am making a mailing postcard
I am having the mailing printed using 4 color foil on certain parts.
I am looking for a design that maximizes the foil process where certain parts are done in foil to grab the customers attention (example: if there is a car on the postcard the headlights would be done in foil) .
I am targeting some industries, (auto, real estate, medical, beauty) I would like the post card to have examples of postcard ideas for 2 or 3 of these industries.
specs:
the postcard should be atleast 6.5x9 up to 8.5x11, I don't want to restrict the space for the creative as I don't want everything to look like a huge mess. both sides will be used.
the piece is a direct mail piece so it has to meet requirements of https://www.mailvantor.com/business/pdf/quick-reference-guide.pdf
text will be
"business with no limits, meet mailing with no addresses, gain new customers through "Open Porch Route Drop" reach new customers at their home without needing their address. "
I also want some current print specials I am running included.
-double your order FREE (order 500 business cards and get 1000)
-250 100lb gloss stock brochures 99.00
-business packages (cards, envelopes and letterhead) 299
-1000 flyers 140.40
-5000 postcards 179.99
A list of services
banners
booklets
brochures
business cards
calendars
catalogs
CD/DVD packages
envelopes
event tickets
flyers
hangtags
postcards
posters
presentation folders
rack cards
labels
table tents
window cling and decal
"order 24/7 orders@inkwillow.com" must be included
my logo is InkWillow will be supplied later
ive received some great designs. however Im looking for something a little more modern like some zorvel would put out. if the amount of words is too much please feel free to edit. also an idea i had for the list of services i offer is to have it transparent yet readable as the background of the postcard some small some big but covering the entire backgroud. you can then design on top of that with other thing. just an early morning thought
Reason: I have uploaded a sketch of my idea, please take time to look at it for an accurate depiction of what im looking for. feel free to add elements that make it pop off the page
Reason: We are getting close i will be providing feed back today

```html
<!DOCTYPE html>
<html lang="en">
<head>
<meta charset="utf-8">
<title>InkWillow Direct Mail Postcard</title>
<link rel="stylesheet" href="https://fonts.googleapis.com/css2?family=Open+Sans:wght@400;600;700;800&display=swap">
<style>
  :root {
    --page: #e9e6e1;
    --navy: #0f1a2e;
    --ink: #0a0a0c;
    --sky: #2aa7dc;
    --lime: #a8cc3a;
    --grey-word: #4d4f55;
    --text-dark: #1b1f16;
    --white: #ffffff;
  }
  * { box-sizing: border-box; margin: 0; padding: 0; }
  html, body { width: 1200px; height: 900px; overflow: hidden; }
  body {
    background: var(--page);
    font-family: "Open Sans", Arial, sans-serif;
    display: flex;
    align-items: center;
    justify-content: center;
    gap: 40px;
  }
  .postcard {
    position: relative;
    width: 560px;
    height: 374px;
    overflow: hidden;
    box-shadow: 0 10px 28px rgba(0,0,0,.28);
  }

  /* Front */
  .postcard--front { background: var(--navy); }
  .band-art { position: absolute; inset: 0; width: 100%; height: 100%; }
  .headline {
    position: absolute; top: 18px; left: 30px; right: 30px;
    color: var(--sky); font-weight: 600; font-size: 15px;
    line-height: 1.3; text-align: center;
  }
  .sample-collage {
    position: absolute; left: 34px; top: 140px; width: 190px; height: 150px;
    transform: rotate(-5deg);
    background: linear-gradient(135deg, #3a8fd6 0%, #f4f4f4 35%, #e9b23b 60%, #d94b4b 80%, #6bc3e8 100%);
    box-shadow: 0 4px 10px rgba(0,0,0,.25);
  }
  .sample-stack {
    position: absolute; right: 18px; top: 108px; width: 82px; height: 130px;
    transform: rotate(-4deg);
    background: linear-gradient(180deg, #d63a3a 0%, #f2f2f2 40%, #f2a33a 65%, #ffffff 100%);
    box-shadow: 0 4px 10px rgba(0,0,0,.25);
  }
  .specials {
    position: absolute; left: 250px; top: 142px; width: 210px;
    list-style: none; color: var(--text-dark);
    font-size: 10.5px; font-weight: 600; line-height: 1.35;
    transform: rotate(-2.2deg);
  }
  .specials li { position: relative; padding-left: 12px; }
  .specials li::before {
    content: ""; position: absolute; left: 0; top: 5px;
    width: 6px; height: 6px; border-radius: 50%; background: var(--ink);
  }
  .specials .note { display: block; font-weight: 400; font-size: 9.5px; }
  .order-line {
    position: absolute; left: 26px; bottom: 14px;
    color: var(--lime); font-weight: 800; font-size: 19px;
  }

  /* Back */
  .postcard--back { background: var(--ink); }
  .service-wall {
    position: absolute; left: 16px; top: 12px; width: 306px;
    font-size: 13px; line-height: 19px; white-space: nowrap;
  }
  .service-wall p { color: var(--grey-word); font-weight: 600; }
  .service-wall p.bright { font-weight: 800; color: var(--white); }
  .service-wall .lime { color: var(--lime); }
  .service-wall .sky { color: var(--sky); }
  .postage-box {
    position: absolute; right: 20px; top: 14px; width: 78px; height: 48px;
    background: var(--white); border: 1px solid #999;
    font-size: 10px; line-height: 1.2; text-align: center; color: #222;
    display: flex; align-items: center; justify-content: center;
  }
  .feature-ring {
    position: absolute; border-radius: 50%; background: var(--white);
    display: flex; align-items: center; justify-content: center;
  }
  .feature-ring .photo { border-radius: 50%; }
  .ring-a { right: 120px; top: 66px; width: 112px; height: 112px; border: 8px solid var(--sky); }
  .ring-a .photo { width: 88px; height: 88px; background: linear-gradient(135deg, #dfeef0, #4fa3a8); }
  .ring-b { right: 16px; top: 78px; width: 94px; height: 94px; border: 7px solid var(--sky); }
  .ring-b .photo { width: 72px; height: 72px; background: linear-gradient(135deg, #f2ee3a, #2a2a2a); }
  .ring-c { right: 132px; top: 186px; width: 68px; height: 68px; border: 6px solid var(--lime); }
  .ring-c .photo { width: 50px; height: 50px; background: linear-gradient(135deg, #8cb8e0, #2c4f7c); }
</style>
</head>
<body>

  <section class="postcard postcard--front" aria-label="Postcard front">
    <svg class="band-art" viewBox="0 0 560 374" aria-hidden="true">
      <polygon points="0,128 560,100 560,106 0,134" fill="#0a0a0c"/>
      <polygon points="0,134 560,106 560,114 0,142" fill="#2aa7dc"/>
      <polygon points="0,142 560,114 560,292 0,316" fill="#a8cc3a"/>
      <polygon points="0,316 560,292 560,302 0,326" fill="#2aa7dc"/>
      <polygon points="0,330 560,306 560,311 0,335" fill="#a8cc3a"/>
    </svg>
    <p class="headline">“ Business with no limits, meet mailing with no addresses,<br>Gain new customers through “Open Porch Route Drop”<br>Reach new customers at their home without needing their address. ”</p>
    <div class="sample-collage" role="img" aria-label="Fanned stack of printed flyers and brochure samples"></div>
    <div class="sample-stack" role="img" aria-label="Stacked sample brochures and envelope"></div>
    <ul class="specials">
      <li>Double your order FREE <span class="note">(order 500 business cards and get 1000)</span></li>
      <li>250 100lb gloss stock brochures 99.00</li>
      <li>Business packages <span class="note">(cards, envelopes and letterhead) 299</span></li>
      <li>1000 flyers 140.40</li>
      <li>5000 postcards 179.99</li>
    </ul>
    <p class="order-line">order 24/7 orders@inkwillow.com</p>
  </section>

  <section class="postcard postcard--back" aria-label="Postcard back">
    <div class="service-wall">
      <p>banners • booklets • brochures</p>
      <p class="bright"><span class="lime">banners</span> • <span class="sky">booklets</span> • <span class="lime">brochures</span></p>
      <p>business cards • calendars • catalogs</p>
      <p class="bright"><span class="sky">business cards</span> • <span class="lime">calendars</span> • <span class="sky">catalogs</span></p>
      <p>CD/DVD packages • envelopes</p>
      <p class="bright"><span class="lime">CD/DVD packages</span> • <span class="sky">envelopes</span></p>
      <p>event tickets • flyers • hangtags</p>
      <p class="bright"><span class="lime">event tickets</span> • <span class="sky">flyers</span> • <span class="lime">hangtags</span></p>
      <p>postcards • posters • rack cards</p>
      <p class="bright"><span class="sky">postcards</span> • <span class="lime">posters</span></p>
      <p class="bright"><span class="sky">presentation folders</span> • <span class="lime">rack cards</span></p>
      <p class="bright"><span class="sky">labels</span> • <span class="lime">table tents</span></p>
      <p class="bright"><span class="sky">window cling and decal</span></p>
    </div>
    <svg class="band-art" viewBox="0 0 560 374" aria-hidden="true">
      <polygon points="0,300 560,262 560,272 0,310" fill="#2aa7dc"/>
      <polygon points="0,310 560,272 560,374 0,374" fill="#0f1a2e"/>
      <polygon points="0,314 560,276 560,282 0,320" fill="#a8cc3a"/>
    </svg>
    <div class="postage-box">Postage<br>Stamp</div>
    <div class="feature-ring ring-a"><div class="photo" role="img" aria-label="Printed brochure sample"></div></div>
    <div class="feature-ring ring-b"><div class="photo" role="img" aria-label="Yellow booklet sample"></div></div>
    <div class="feature-ring ring-c"><div class="photo" role="img" aria-label="Presentation folder sample"></div></div>
    <p class="order-line">order 24/7 orders@inkwillow.com</p>
  </section>

</body>
</html>
```